Business Card

Just need business logo with phone number on it. 0487 312 654
And the following on the bottom of the card.

"Your local plumbing experts".
and emblems for zelpa card, cheque and cash

```html
<!DOCTYPE html>
<html lang="en">
<head>
<meta charset="utf-8">
<title>Ridgeline Plumbing &amp; Drainage – Business Card</title>
<link href="https://fonts.googleapis.com/css2?family=Roboto:wght@400;500;900&display=swap" rel="stylesheet">
<style>
  :root {
    --backdrop: #e9e6e1;
    --card-white: #ffffff;
    --card-shade: #f1f2f3;
    --brand-red: #e0263a;
    --brand-blue: #1fa3d6;
    --deep-blue: #1a8cc0;
    --ink-navy: #1d3f8a;
    --icon-slate: #55606d;
    --cash-green: #3d9a4a;
  }
  html, body {
    margin: 0;
    width: 1200px;
    height: 780px;
    overflow: hidden;
    background: var(--backdrop);
    font-family: "Roboto", Arial, sans-serif;
  }
  .canvas {
    position: relative;
    width: 1200px;
    height: 780px;
  }
  .card {
    position: absolute;
    left: 75px;
    top: 90px;
    width: 1050px;
    height: 600px;
    background: linear-gradient(160deg, var(--card-white) 55%, var(--card-shade));
    box-shadow: 0 14px 40px rgba(0,0,0,.18);
    overflow: hidden;
  }
  .card-art {
    position: absolute;
    inset: 0;
  }
  .brand {
    position: absolute;
    left: 270px;
    top: 190px;
    display: flex;
    align-items: center;
    gap: 18px;
  }
  .brand-dot {
    width: 26px;
    height: 26px;
    border-radius: 50%;
    background: var(--brand-red);
  }
  .brand-name {
    margin: 0;
    color: var(--brand-red);
    font-weight: 900;
    font-size: 54px;
    line-height: 1;
    letter-spacing: 1px;
  }
  .brand-name span {
    display: block;
    font-size: 24px;
    letter-spacing: 6px;
    margin-top: 8px;
  }
  .phone {
    position: absolute;
    left: 315px;
    top: 318px;
    margin: 0;
    font-size: 40px;
    font-weight: 500;
    color: var(--brand-blue);
  }
  .phone .label { color: var(--brand-red); }
  .payments {
    position: absolute;
    left: 340px;
    top: 396px;
    display: flex;
    align-items: center;
    gap: 56px;
  }
  .pay-card {
    width: 92px;
    height: 58px;
    border: 2px solid #c9ced6;
    border-radius: 6px;
    background: var(--card-white);
    display: flex;
    align-items: center;
    justify-content: center;
    font-weight: 900;
    font-size: 24px;
    color: var(--ink-navy);
  }
  .tagline {
    position: absolute;
    left: 0;
    right: 0;
    bottom: 20px;
    margin: 0;
    text-align: center;
    color: var(--card-white);
    font-size: 26px;
    font-weight: 400;
    letter-spacing: 1px;
  }
</style>
</head>
<body>
<main class="canvas">
  <section class="card">
    <svg class="card-art" width="1050" height="600" viewBox="0 0 1050 600" aria-hidden="true">
      <!-- top swoosh bands -->
      <path d="M300,0 H1050 V46 C820,46 600,58 420,92 C270,120 130,170 0,230 V150 C150,80 320,30 460,0 Z" fill="var(--brand-red)"/>
      <path d="M0,0 H560 C380,36 170,96 0,170 Z" fill="var(--brand-blue)"/>
      <path d="M0,262 C150,190 300,140 470,110" fill="none" stroke="var(--brand-red)" stroke-width="4"/>
      <!-- bottom band -->
      <rect x="0" y="518" width="1050" height="3" fill="var(--brand-red)"/>
      <rect x="0" y="530" width="1050" height="70" fill="var(--brand-blue)"/>
    </svg>

    <div class="brand">
      <div class="brand-dot"></div>
      <h1 class="brand-name">RIDGELINE<span>PLUMBING &amp; DRAINAGE</span></h1>
    </div>

    <p class="phone"><span class="label">P:</span> 0487 312 654</p>

    <div class="payments">
      <div class="pay-card">ZELPA</div>
      <svg class="pay-icon cash-icon" width="70" height="70" viewBox="0 0 70 70" role="img" aria-label="Cash">
        <circle cx="35" cy="35" r="33" fill="var(--icon-slate)"/>
        <rect x="14" y="24" width="42" height="22" rx="3" fill="var(--cash-green)"/>
        <circle cx="35" cy="35" r="6" fill="#d8f0d8"/>
      </svg>
      <svg class="pay-icon cheque-icon" width="90" height="62" viewBox="0 0 90 62" role="img" aria-label="Cheque">
        <rect x="3" y="6" width="84" height="50" rx="5" fill="var(--icon-slate)"/>
        <rect x="10" y="13" width="70" height="36" rx="3" fill="#ffffff"/>
        <text x="16" y="40" font-family="Roboto, sans-serif" font-weight="900" font-size="20" fill="var(--deep-blue)">$</text>
        <rect x="36" y="22" width="36" height="4" fill="var(--deep-blue)"/>
        <rect x="36" y="31" width="36" height="4" fill="var(--deep-blue)"/>
        <rect x="36" y="40" width="24" height="4" fill="var(--deep-blue)"/>
      </svg>
    </div>

    <p class="tagline">Your local plumbing experts</p>
  </section>
</main>
</body>
</html>
```